MRT Property - Business Cards

Looking for a business card & general letterhead, signage etc design for our new logo.

Colours:
000a20
0056a2
00b5ef
0088ce
68cef2

Fonts:
Poppins
Karla

Please keep look and feel of new brand - example in the zip package I sent.

```html
<!DOCTYPE html>
<html lang="en">
<head>
<meta charset="utf-8">
<title>MRT Property Letterhead</title>
<link href="https://fonts.googleapis.com/css2?family=Poppins:wght@400;600&display=swap" rel="stylesheet">
<style>
  :root {
    --navy: #000a20;
    --brand-blue: #0056a2;
    --sky: #00b5ef;
    --mid-blue: #0088ce;
    --light-sky: #68cef2;
    --paper: #ffffff;
    --backdrop: #919095;
  }
  * { margin: 0; padding: 0; box-sizing: border-box; }
  html, body {
    width: 1200px;
    height: 792px;
    overflow: hidden;
    background: var(--backdrop);
    font-family: "Poppins", sans-serif;
  }
  .letterhead {
    position: absolute;
    left: 331px;
    top: 16px;
    width: 875px;
    height: 1238px;
    background: var(--paper);
    transform: scale(0.6139);
    transform-origin: top left;
    overflow: hidden;
    box-shadow: -14px 10px 40px rgba(0, 10, 32, 0.35);
  }
  .brand {
    position: absolute;
    top: 52px;
    left: 0;
    width: 100%;
    display: flex;
    justify-content: center;
    align-items: center;
    gap: 18px;
  }
  .brand-dot {
    width: 46px;
    height: 46px;
    border-radius: 50%;
    background: var(--sky);
  }
  .brand-name {
    font-family: "Poppins", sans-serif;
    font-weight: 600;
    font-size: 60px;
    line-height: 1;
    color: var(--brand-blue);
  }
  .footer-wave {
    position: absolute;
    left: 0;
    bottom: 0;
    width: 875px;
    height: 300px;
    display: block;
  }
  .contact {
    position: absolute;
    left: 44px;
    top: 1058px;
    color: var(--paper);
    font-size: 20px;
    line-height: 24px;
    font-weight: 400;
  }
  .contact-row {
    display: flex;
    align-items: flex-start;
    gap: 12px;
  }
  .contact-row + .contact-row { margin-top: 1px; }
  .contact-row.address { margin-bottom: 13px; }
  .contact-icon {
    width: 15px;
    height: 15px;
    margin-top: 4px;
    flex: none;
  }
</style>
</head>
<body>
  <main class="letterhead">
    <header class="brand">
      <span class="brand-dot"></span>
      <span class="brand-name">MRT Property</span>
    </header>

    <svg class="footer-wave" viewBox="0 0 875 300" aria-hidden="true">
      <defs>
        <linearGradient id="waveBack" x1="0" x2="1" y1="0" y2="0">
          <stop offset="0" stop-color="var(--light-sky)"/>
          <stop offset="0.5" stop-color="#3ec3f0"/>
          <stop offset="1" stop-color="var(--sky)"/>
        </linearGradient>
      </defs>
      <path d="M0,112 C40,62 95,50 135,51 C250,54 350,118 460,170 C560,215 640,236 705,236 C800,236 858,182 875,141 L875,300 L0,300 Z" fill="url(#waveBack)"/>
      <path d="M0,151 C50,102 110,88 170,86 C270,86 360,140 450,185 C560,238 640,262 720,262 C800,262 850,232 875,211 L875,300 L0,300 Z" fill="var(--mid-blue)"/>
      <path d="M0,151 C50,102 110,88 170,86 C270,86 360,140 450,185 C560,238 640,262 720,262 C800,262 850,232 875,211" fill="none" stroke="var(--paper)" stroke-width="7"/>
    </svg>

    <address class="contact" style="font-style: normal;">
      <div class="contact-row address">
        <svg class="contact-icon" viewBox="0 0 16 16" aria-hidden="true"><path d="M8 1a5 5 0 0 0-5 5c0 3.6 5 9 5 9s5-5.4 5-9a5 5 0 0 0-5-5zm0 7a2 2 0 1 1 0-4 2 2 0 0 1 0 4z" fill="none" stroke="#fff" stroke-width="1.5"/></svg>
        <span>Suite 4.12, Level 4<br>18 Harbourline Road, Sydney,<br>Riverside Park NSW 2150</span>
      </div>
      <div class="contact-row">
        <svg class="contact-icon" viewBox="0 0 16 16" aria-hidden="true"><path d="M4 1.5l2.2 2.8-1.4 1.6a9 9 0 0 0 5.3 5.3l1.6-1.4 2.8 2.2-1.6 2.4C7.5 14.2 1.8 8.5 1.6 3.1z" fill="#fff"/></svg>
        <span>+61 2 9000 4821</span>
      </div>
      <div class="contact-row">
        <svg class="contact-icon" viewBox="0 0 16 16" aria-hidden="true"><circle cx="8" cy="8" r="6.5" fill="none" stroke="#fff" stroke-width="1.5"/><path d="M1.5 8h13M8 1.5c2 2 2 11 0 13M8 1.5c-2 2-2 11 0 13" fill="none" stroke="#fff" stroke-width="1.2"/></svg>
        <span>www.mrtproperty.com.au</span>
      </div>
      <div class="contact-row">
        <svg class="contact-icon" viewBox="0 0 16 16" aria-hidden="true"><rect x="1.5" y="3.5" width="13" height="10" rx="1" fill="none" stroke="#fff" stroke-width="1.5"/><path d="M1.5 4.5 8 9.5l6.5-5" fill="none" stroke="#fff" stroke-width="1.5"/></svg>
        <span>info@mrtproperty.com.au</span>
      </div>
    </address>
  </main>
</body>
</html>
```